Business Card for Multi-Brand Sportswear Company

We are looking for a business card which represents our company and the multiple brands within it.

The company: Fen Athletics (LTD)
The brands: Fen, TavaPuni, ElmStretch, Grit and Rain

Employees using these cards would be representing Fen Athletics, rather than any of the individual brands. You will see a current design within the uploaded files, to give some inspiration. The actual text of the brands is not necessary, but the logos should be on there is some format.

Our creative minds on this are stretched, so we are looking for someone to make this their own, and show us what a good business card should look like.

We may like to get these printed with spot gloss, so keep that in mind with your designs.

www.fenathletics.co.uk

Industry/Entity Type

Business

Contact Information for Business Card

Leo Pemberton-Hale
Operations Manager
(+44) 1632 960 418
Leo@fenathletics.co.uk
www.fenathletics.co.uk

Font styles to use
Sans Serif
Other font styles liked:
• Eurostile

Colors
ffffff

Requirements
Nice to have
• Dark (black) background

```html
<!DOCTYPE html>
<html lang="en">
<head>
<meta charset="utf-8">
<title>Fen Athletics – Business Card</title>
<link rel="stylesheet" href="https://fonts.googleapis.com/css2?family=Open+Sans:wght@400;600;700&display=swap">
<style>
  :root {
    --backdrop: #e6e6e6;
    --card: #000000;
    --white: #ffffff;
    --grey: #c8c8c8;
    --muted: #9a9a9a;
    --accent-red: #c8202a;
    --accent-teal: #1aa39a;
  }
  * { margin: 0; padding: 0; box-sizing: border-box; }
  html, body {
    width: 1200px; height: 900px; overflow: hidden;
    background: var(--backdrop);
    font-family: "Open Sans", Arial, sans-serif;
  }
  .stage { position: relative; width: 1200px; height: 900px; }
  .card {
    position: absolute; top: 275px; width: 477px; height: 294px;
    background: var(--card); color: var(--white);
  }
  .card--front { left: 116px; border-radius: 0 60px 0 60px; }
  .card--back  { left: 622px; border-radius: 60px 0 60px 0; }

  .wordmark { position: absolute; line-height: 1; }
  .wordmark__name { display: block; font-weight: 600; letter-spacing: 0.02em; }
  .wordmark__tag { display: block; font-weight: 400; letter-spacing: 0.14em; }

  .card--front .wordmark { left: 21px; top: 45px; }
  .card--front .wordmark__name { font-size: 24px; color: var(--grey); }
  .card--front .wordmark__tag { font-size: 7px; margin-top: 5px; color: var(--grey); padding-left: 2px; }

  .holder { position: absolute; right: 21px; top: 157px; text-align: right; }
  .holder__name { font-size: 15px; font-weight: 700; letter-spacing: 0.02em; }
  .holder__role { font-size: 13px; margin-top: 1px; }

  .divider { position: absolute; left: 0; right: 0; top: 202px; height: 1.5px; background: var(--accent-red); }

  .address { position: absolute; left: 20px; top: 216px; font-size: 12px; line-height: 17px; }

  .contacts { position: absolute; right: 21px; top: 214px; list-style: none; }
  .contacts li {
    display: flex; justify-content: flex-end; align-items: center;
    font-size: 12.5px; line-height: 19px; gap: 9px;
  }
  .contacts li.is-muted { color: var(--grey); }
  .contacts svg { width: 11px; height: 11px; flex: none; }

  .card--back .wordmark { left: 0; right: 0; top: 136px; text-align: center; }
  .card--back .wordmark__name { font-size: 34px; }
  .card--back .wordmark__tag { font-size: 8px; margin-top: 6px; color: var(--grey); }

  .brands {
    position: absolute; left: 80px; right: 80px; top: 226px;
    display: flex; justify-content: space-between; align-items: center;
    list-style: none;
  }
  .brands li { font-size: 11px; font-weight: 600; color: var(--white); display: flex; align-items: center; gap: 5px; }
  .brand-dot { width: 7px; height: 7px; border-radius: 50%; background: var(--accent-red); }
</style>
</head>
<body>
<main class="stage">
  <section class="card card--front" aria-label="Card front">
    <div class="wordmark">
      <span class="wordmark__name">FEN ATHLETICS</span>
      <span class="wordmark__tag">PERFORMANCE WEAR</span>
    </div>
    <div class="holder">
      <p class="holder__name">LEO PEMBERTON-HALE</p>
      <p class="holder__role">Managing Director</p>
    </div>
    <div class="divider"></div>
    <p class="address">Marsh Lane,<br>Elmwick,Fenby,ZZ9 4QT</p>
    <ul class="contacts">
      <li>+44(0)1632 960418
        <svg viewBox="0 0 12 12" aria-hidden="true"><rect x="3" y="0.5" width="6" height="11" rx="1.2" fill="none" stroke="var(--accent-teal)" stroke-width="1.2"/><circle cx="6" cy="9.6" r="0.7" fill="var(--accent-teal)"/></svg>
      </li>
      <li class="is-muted">leo@fenathletics.co.uk
        <svg viewBox="0 0 12 12" aria-hidden="true"><rect x="0.5" y="2.5" width="11" height="7" fill="var(--accent-teal)"/><path d="M0.5 2.5 L6 6.5 L11.5 2.5" fill="none" stroke="#000" stroke-width="0.9"/></svg>
      </li>
      <li class="is-muted">www.fenathletics.co.uk
        <svg viewBox="0 0 12 12" aria-hidden="true"><g fill="none" stroke="var(--accent-teal)" stroke-width="1.3" stroke-linecap="round"><path d="M5 7 L7 5"/><path d="M6.2 3.4 L7.6 2 a2 2 0 0 1 2.8 2.8 L9 6.2"/><path d="M5.8 8.6 L4.4 10 a2 2 0 0 1 -2.8 -2.8 L3 5.8"/></g></svg>
      </li>
    </ul>
  </section>

  <section class="card card--back" aria-label="Card back">
    <div class="wordmark">
      <span class="wordmark__name">FEN ATHLETICS</span>
      <span class="wordmark__tag">PERFORMANCE WEAR</span>
    </div>
    <ul class="brands">
      <li>Fen</li>
      <li><span class="brand-dot"></span>Grit and Rain</li>
      <li>TavaPuni</li>
      <li>ElmStretch</li>
    </ul>
  </section>
</main>
</body>
</html>
```